Business card for my new company (Accounting firm)

I need a business card for my new business Brightwell Advisory and Ledger SA. Our services are accounting, tax, audit and financial management. Our customers are small companies, start-ups and new companies. The final design has to show financial security, trust and growth. Please find our logo attached to the business card. Text for the business card: Brightwell Advisory and Ledger SA Tomas Varenholt Director and Founder Certified Accountant Tel. 022 418 57 34 tv@clairevalconseil.ch www.clairevalconseil.ch Rue des Vergières 27 1201 Geneva
Target Market(s)
Our customers are small companies, start-ups and new companies.
Industry/Entity Type
Finance And Accounting
Contact Information for Business Card
Claireval Conseil et Comptes SA
Tomas Varenholt
Directeur et Fondateur
Expert-comptable diplômé
Tél. 022 418 57 34
tv@clairevalconseil.ch
www.clairevalconseil.ch
Rue des Vergières 27
1201 Genève

```html
<!DOCTYPE html>
<html lang="fr">
<head>
<meta charset="utf-8">
<title>Claireval Conseil et Comptes SA – Carte de visite</title>
<link rel="stylesheet" href="https://fonts.googleapis.com/css2?family=Lato:wght@400;700&display=swap">
<style>
  :root {
    --bg: #161719;
    --card: #1e1f22;
    --blue: #1f8ad6;
    --blue-light: #2ea9e3;
    --white: #ffffff;
    --text: #e9ecef;
  }
  * { box-sizing: border-box; margin: 0; padding: 0; }
  html, body { width: 1200px; height: 912px; overflow: hidden; background: var(--bg); }
  body { position: relative; font-family: "Lato", Arial, sans-serif; color: var(--text); }

  .card {
    position: absolute;
    width: 580px;
    height: 332px;
    background: var(--card);
    overflow: hidden;
  }
  .card::after {
    content: "";
    position: absolute;
    left: 0; right: 0; bottom: 0;
    height: 9px;
    background: var(--blue);
  }
  .card--front { left: 50px; top: 100px; }
  .card--back { left: 570px; top: 480px; }

  .brand {
    display: flex;
    align-items: center;
    gap: 12px;
  }
  .brand__mark {
    width: 22px;
    height: 22px;
    background: var(--blue-light);
  }
  .brand__name {
    font-weight: 700;
    color: var(--white);
    letter-spacing: 0.04em;
    line-height: 1.1;
  }

  .card--front .brand {
    position: absolute;
    left: 0; right: 0; top: 108px;
    justify-content: center;
  }
  .card--front .brand__name { font-size: 34px; }
  .front__web {
    position: absolute;
    left: 0; right: 0; top: 232px;
    text-align: center;
    font-size: 17px;
    color: var(--white);
  }

  .card--back .brand {
    position: absolute;
    left: 34px; top: 140px;
    flex-direction: column;
    align-items: flex-start;
    gap: 10px;
  }
  .card--back .brand__name { font-size: 26px; }
  .divider {
    position: absolute;
    left: 292px; top: 50px;
    width: 1.5px; height: 214px;
    background: var(--blue);
  }
  .details {
    position: absolute;
    left: 314px; top: 46px;
    font-size: 13.5px;
    line-height: 1.32;
    color: var(--text);
  }
  .details__name {
    font-size: 20px;
    font-weight: 700;
    color: var(--blue);
    margin-bottom: 2px;
  }
  .details__block { margin-bottom: 9px; }
  .contact { list-style: none; }
  .contact li { display: flex; align-items: center; gap: 9px; }
  .contact svg { width: 12px; height: 12px; fill: var(--blue); flex: none; }
</style>
</head>
<body>
  <section class="card card--front" aria-label="Recto">
    <div class="brand">
      <span class="brand__mark"></span>
      <span class="brand__name">CLAIREVAL</span>
    </div>
    <p class="front__web">www.clairevalconseil.ch</p>
  </section>

  <section class="card card--back" aria-label="Verso">
    <div class="brand">
      <span class="brand__mark"></span>
      <span class="brand__name">CLAIREVAL</span>
    </div>
    <span class="divider"></span>
    <div class="details">
      <p class="details__name">Tomas Varenholt</p>
      <p class="details__block">Directeur et Fondateur<br>Expert-comptable diplômé</p>
      <p class="details__block">Claireval Conseil et Comptes SA<br>Rue des Vergières 27<br>1201 Genève</p>
      <ul class="contact">
        <li>
          <svg viewBox="0 0 24 24" aria-hidden="true"><path d="M6.6 10.8a15.1 15.1 0 0 0 6.6 6.6l2.2-2.2a1 1 0 0 1 1-.25 11.4 11.4 0 0 0 3.6.57 1 1 0 0 1 1 1V20a1 1 0 0 1-1 1A17 17 0 0 1 3 4a1 1 0 0 1 1-1h3.5a1 1 0 0 1 1 1c0 1.25.2 2.45.57 3.57a1 1 0 0 1-.25 1z"/></svg>
          022 418 57 34
        </li>
        <li>
          <svg viewBox="0 0 24 24" aria-hidden="true"><path d="M2 5h20v14H2z M2 5l10 8 10-8" /></svg>
          tv@clairevalconseil.ch
        </li>
        <li>
          <svg viewBox="0 0 24 24" aria-hidden="true"><circle cx="12" cy="12" r="10"/></svg>
          www.clairevalconseil.ch
        </li>
      </ul>
    </div>
  </section>
</body>
</html>
```